Popup Nightclub Grand Opening Flyer

We need to design a flyer for the grand opening of an upscale, exclusive nightclub called "Lantern". The design needs to be chic and exclusive. The background should be black and the text should primarily be white. We like minimalist designs.

Here is the text for the flyer
-
Velvetroll Atlanta Presents

Lantern (LOGO)

A Popup Nightclub Experience
For one night Only

Friday, October 18, 2013
Party begins at 9PM

INVITE ONLY

See invitation for location details
(Velvetroll Atlanta logo)

-
Examples we like

http://cdn4-x.pressfolio-example.com/sites/default/files/styles/image_content_width/hash/3b/fd/2468013579_4421_flyer.jpg?itok=K9rtQw2z

http://files.hubspace-example.net/files/8Hqq-Tr72WWE3kaRbTmcxP5QZK2F396J8nbRw4CKMHfdX2Y7qSEF-MqjxDoNrLY3QCyQJD7npjGaRq3k-Mhx6hqf3MDSWf8r3/2zenSaturdays.jpg

http://morvex-example.com/wp-content/uploads/siteskin/widgetkit/gallery/2zen/2zen-gen_qstay4-01.jpg

Hi All, one thing that we are seeing that we don't like is on over emphasis on the phrase "a popup nightclub experience" please don't make this the largest thing on the flyer

Target Market(s)

Target market is 25-35 year olds who are affluent (rich) and like luxury brands

Requirements
Must have
• Dark Background
Nice to have
• Velvetroll Logo on the bottom
Modern text that isn't curvy
Should not have
• Curved text

```html
<!DOCTYPE html>
<html lang="en">
<head>
<meta charset="utf-8">
<title>Lantern Nightclub — A Popup Nightclub Experience</title>
<link rel="stylesheet" href="https://fonts.googleapis.com/css2?family=Questrial&family=Barlow:wght@300;400&family=Barlow+Condensed:wght@300;500;600&display=swap">
<style>
  :root {
    --ink: #000000;
    --white: #ffffff;
    --silver-light: #f2f2f2;
    --silver-mid: #b9b9b9;
    --silver-dark: #8a8a8a;
    --muted: #b5b5b5;
    --glow: rgba(70, 58, 52, 0.55);
    --petal: rgba(60, 46, 40, 0.45);
  }
  * { margin: 0; padding: 0; box-sizing: border-box; }
  html, body { width: 867px; height: 1200px; overflow: hidden; background: var(--ink); }

  .flyer {
    position: relative;
    width: 867px;
    height: 1200px;
    background: var(--ink);
    color: var(--white);
    overflow: hidden;
  }

  .ornament {
    position: absolute;
    inset: 0;
    background:
      radial-gradient(ellipse 190px 150px at 50% 52%, var(--glow), transparent 75%),
      radial-gradient(ellipse 330px 120px at 50% 30%, var(--petal), transparent 70%),
      radial-gradient(ellipse 260px 180px at 50% 13%, rgba(50, 40, 36, 0.35), transparent 70%),
      radial-gradient(ellipse 360px 140px at 50% 76%, rgba(50, 40, 36, 0.35), transparent 70%);
  }

  .line { position: absolute; left: 0; width: 100%; text-align: center; white-space: nowrap; }

  .presenter { top: 86px; font-family: "Questrial", sans-serif; font-size: 33px; letter-spacing: 0.5px; }
  .presents  { top: 132px; font-family: "Questrial", sans-serif; font-size: 25px; letter-spacing: 7px; }

  .brand-mark {
    position: absolute;
    left: 50%;
    top: 196px;
    width: 84px;
    height: 84px;
    margin-left: -42px;
    border-radius: 50%;
    background: linear-gradient(180deg, var(--silver-light), var(--silver-dark));
  }
  .brand-name { top: 296px; font-family: "Questrial", sans-serif; font-size: 72px; line-height: 86px; letter-spacing: 10px; padding-left: 10px; }
  .brand-sub  { top: 388px; font-family: "Questrial", sans-serif; font-size: 22px; letter-spacing: 5px; padding-left: 5px; }

  .rule {
    position: absolute;
    left: 294px;
    width: 280px;
    height: 2px;
    background: linear-gradient(90deg, transparent, var(--silver-mid) 20%, var(--white) 50%, var(--silver-mid) 80%, transparent);
  }
  .rule--top { top: 506px; }
  .rule--mid { top: 694px; }
  .rule--bottom { top: 748px; }

  .headline {
    position: absolute;
    top: 516px;
    left: 0;
    width: 100%;
    text-align: center;
    font-family: "Barlow Condensed", sans-serif;
    font-weight: 600;
    font-size: 52px;
    line-height: 57px;
    letter-spacing: 0.5px;
    background: linear-gradient(180deg, var(--white) 0%, var(--silver-mid) 55%, var(--silver-light) 100%);
    -webkit-background-clip: text;
    background-clip: text;
    color: transparent;
  }
  .tagline { top: 703px; font-family: "Barlow", sans-serif; font-weight: 300; font-size: 26px; letter-spacing: 1px; }

  .dotted {
    position: absolute;
    left: 270px;
    width: 326px;
    border-top: 2px dotted var(--silver-mid);
  }
  .dotted--top { top: 848px; }
  .dotted--bottom { top: 930px; }
  .date { top: 855px; font-family: "Barlow Condensed", sans-serif; font-weight: 600; font-size: 32px; }
  .time { top: 887px; font-family: "Barlow Condensed", sans-serif; font-weight: 300; font-size: 32px; letter-spacing: 0.5px; }

  .invite { top: 955px; font-family: "Barlow Condensed", sans-serif; font-weight: 500; font-size: 22px; letter-spacing: 6px; padding-left: 6px; }

  .location-note { top: 1022px; font-family: "Questrial", sans-serif; font-size: 17px; color: var(--muted); letter-spacing: 0.5px; }

  .host {
    position: absolute;
    top: 1064px;
    left: 0;
    width: 100%;
    display: flex;
    justify-content: center;
    align-items: center;
    gap: 14px;
  }
  .host__square { width: 26px; height: 26px; background: var(--silver-light); }
  .host__name { font-family: "Questrial", sans-serif; font-size: 24px; letter-spacing: 4px; color: var(--white); }
</style>
</head>
<body>
  <main class="flyer">
    <div class="ornament" role="img" aria-label="Faint dark bronze petal ornament radiating around the centre of the flyer"></div>

    <p class="line presenter">VELVETROLL Atlanta</p>
    <p class="line presents">Presents</p>

    <div class="brand-mark" aria-hidden="true"></div>
    <h1 class="line brand-name">LANTERN</h1>
    <p class="line brand-sub">NIGHTCLUB</p>

    <span class="rule rule--top"></span>
    <h2 class="headline">A POPUP<br>NIGHTCLUB<br>EXPERIENCE</h2>
    <span class="rule rule--mid"></span>
    <p class="line tagline">For one night only</p>
    <span class="rule rule--bottom"></span>

    <span class="dotted dotted--top"></span>
    <p class="line date">FRIDAY, OCTOBER 18, 2013</p>
    <p class="line time">PARTY BEGINS AT 9PM</p>
    <span class="dotted dotted--bottom"></span>

    <p class="line invite">INVITE ONLY</p>

    <p class="line location-note">See invitation for location details</p>

    <div class="host">
      <span class="host__square" aria-hidden="true"></span>
      <span class="host__name">VELVETROLL ATLANTA</span>
    </div>
  </main>
</body>
</html>
```